Dovecote Realty

Business cards for 4 people

They need to say for all
87 Tarrow Quay, Boston MA 02114

Each person will have their own personal information
We would like gold embossing for the name of the company
Marla is the blonde sitting in the chair smiling her information should be on the back of the card with her name and information
Should say for slogan classic pattern, elevated experience
marla@dovecoteprops.com
(413) 555-0182

Odette is the brunette with wavy hair in the tan suit celina@dovecoteprops.com
(617) 555-0137

faith@dovecoteprops.com
(413) 555-0164
standing next to the chair

hope@dovecoteprops.com
(413) 555-0199
close up headshot

```html
<!DOCTYPE html>
<html lang="en">
<head>
<meta charset="utf-8">
<title>Dovecote Realty — Business Cards</title>
<link rel="stylesheet" href="https://fonts.googleapis.com/css2?family=Libre+Baskerville:wght@700&family=Montserrat:wght@400&display=swap">
<style>
  :root {
    --backdrop: #1d1d1f;
    --card-white: #f4f4f3;
    --navy: #22324f;
    --gold: #e2b25e;
    --ink: #3b3b3b;
    --photo-dark: #2a2626;
    --photo-warm: #8a5a34;
  }
  * { margin: 0; padding: 0; box-sizing: border-box; }
  html, body { width: 1200px; height: 1059px; overflow: hidden; background: var(--backdrop); }
  .canvas { position: relative; width: 1200px; height: 1059px; }

  .card {
    position: absolute;
    border-radius: 18px;
    overflow: hidden;
    box-shadow: 0 10px 26px rgba(0,0,0,.55);
  }
  .card--front { left: 257px; top: 89px; width: 687px; height: 390px; background: var(--card-white); }
  .card--back  { left: 254px; top: 547px; width: 693px; height: 393px; background: var(--navy); }

  .wordmark {
    position: absolute;
    font-family: "Libre Baskerville", serif;
    font-weight: 700;
    color: var(--gold);
    line-height: 1;
    white-space: nowrap;
    text-align: center;
  }
  .card--front .wordmark { left: 20px; width: 240px; top: 110px; font-size: 19px; letter-spacing: .5px; }
  .card--back .wordmark { left: 0; width: 693px; top: 176px; font-size: 40px; letter-spacing: 1px; }

  .accent-bar { position: absolute; left: 0; top: 192px; width: 18px; height: 40px; background: var(--gold); }

  .person-name {
    position: absolute; left: 38px; top: 186px;
    font-family: "Libre Baskerville", serif; font-weight: 700;
    font-size: 21px; color: var(--gold); letter-spacing: .3px; white-space: nowrap;
  }
  .person-title {
    position: absolute; left: 38px; top: 217px;
    font-family: "Montserrat", sans-serif; font-size: 15.5px; color: var(--ink); white-space: nowrap;
  }
  .contact-list { position: absolute; left: 37px; top: 259px; list-style: none; }
  .contact-item {
    display: flex; align-items: center; height: 25px;
    font-family: "Montserrat", sans-serif; font-size: 15.5px; color: var(--ink); white-space: nowrap;
  }
  .contact-icon { width: 13px; height: 13px; margin-right: 8px; flex: none; fill: var(--gold); }

  .portrait {
    position: absolute; left: 432px; top: 35px; width: 250px; height: 355px;
    border-radius: 120px 120px 0 0;
    background: linear-gradient(180deg, #d9bf8c 0%, var(--photo-dark) 30%, var(--photo-dark) 70%, var(--photo-warm) 100%);
    opacity: .9;
  }
</style>
</head>
<body>
<main class="canvas">

  <section class="card card--front" aria-label="Business card front">
    <p class="wordmark">DOVECOTE REALTY</p>

    <div class="accent-bar"></div>
    <h1 class="person-name">MARLA ASHCOMBE</h1>
    <p class="person-title">Real Estate Advisor and Rentals Manager</p>

    <ul class="contact-list">
      <li class="contact-item">
        <svg class="contact-icon" viewBox="0 0 24 24"><path d="M6.6 10.8a15.1 15.1 0 0 0 6.6 6.6l2.2-2.2a1 1 0 0 1 1-.25 11.4 11.4 0 0 0 3.6.57 1 1 0 0 1 1 1V20a1 1 0 0 1-1 1A17 17 0 0 1 3 4a1 1 0 0 1 1-1h3.5a1 1 0 0 1 1 1c0 1.25.2 2.45.57 3.57a1 1 0 0 1-.25 1z"/></svg>
        (413) 555-0182
      </li>
      <li class="contact-item">
        <svg class="contact-icon" viewBox="0 0 24 24"><path d="M2 9l10-7 10 7v12H2zM4 10v.2l8 5.6 8-5.6V10l-8-5.6z"/></svg>
        marla@dovecoteprops.com
      </li>
      <li class="contact-item">
        <svg class="contact-icon" viewBox="0 0 24 24"><path d="M12 2a10 10 0 1 0 0 20 10 10 0 0 0 0-20zm0 2a8 8 0 0 1 6.9 4H15l-2 2 1 3-3 2v3l-2 1a8 8 0 0 1-4.8-9.5L7 11l2-1V7l3-3z"/></svg>
        www.dovecoteprops.com
      </li>
      <li class="contact-item">
        <svg class="contact-icon" viewBox="0 0 24 24"><path d="M12 1a8 8 0 0 0-8 8c0 6 8 14 8 14s8-8 8-14a8 8 0 0 0-8-8zm0 11a3 3 0 1 1 0-6 3 3 0 0 1 0 6z"/></svg>
        87 Tarrow Quay, Boston MA 02114
      </li>
    </ul>

    <div class="portrait" role="img" aria-label="Photo of Marla, smiling, seated on a wooden chair in a black suit"></div>
  </section>

  <section class="card card--back" aria-label="Business card back">
    <p class="wordmark">DOVECOTE REALTY</p>
  </section>

</main>
</body>
</html>
```